Talon Microsystems PowerPoint Master Slide Deck Design

This is a 2-phase project to design a slide deck for a semiconductor company in the Silicon Valley. The design budget will be increased with each phase.
The slide deck will need to have one version with a dark background for presentations and a second version with a white background. Otherwise, the slides will be the same. I anticipate we will need a total of 10 slides, but that number may change.
The first phase will be to design a Title and a Title and Content slide.
- The Title Slide is the first slide of the deck. It should include the presentation title, the presenter's name and date of presentation
- The Title and Content slide should include a title and content with bullet points and up to 2 additional sub-bullets
- The Title and Content slide should have a footer that includes the slide #, Talon Microsystems Confidential, and the logo. This footer will be on every slide except the Title Slide
The first two slides will serve as the format for the remaining ~8 slides:
-Header and Content Text (1, 2, 4 column)
-Header and Content Image (bar chart, pie chart, tables)
-Break
-Title only
-Closing (Talon logo only)
Our slides contain a lot of content so a clean and simple design is best.
Both phases will need to include pre-set color options for
-Text and Lines
-Shadows
-Bullets and sub-bullets (including shapes, ex. circle, slash, square, etc.)
-Bar charts, pie charts, tables
Samples of our collateral are attached. Logo files are also attached
Look and feel
Each slider illustrates characteristics of the customer's brand and the style your logo design should communicate.

```html
<!DOCTYPE html>
<html lang="en">
<head>
<meta charset="utf-8">
<title>Talon Microsystems – Master Slide Deck</title>
<link href="https://fonts.googleapis.com/css2?family=Montserrat:wght@300;400;600;700&display=swap" rel="stylesheet">
<style>
:root{
  --ink:#03040d;
  --ink-2:#070a1c;
  --blue:#1f5bff;
  --royal:#1433e0;
  --cyan:#1fc0ff;
  --sky:#3e8bff;
  --white:#ffffff;
  --muted:#aab2c8;
  --body:#c4c9dc;
  --page:#ffffff;
}
*{box-sizing:border-box;margin:0;padding:0}
html,body{width:1200px;height:1200px;overflow:hidden;background:var(--page)}
body{font-family:"Montserrat",sans-serif;position:relative}
.slide{position:absolute;width:364px;height:204px;transform:scale(.625);transform-origin:0 0;background:var(--ink);overflow:hidden;border-top:1px solid var(--blue);border-bottom:2px solid var(--blue);box-shadow:0 6px 14px rgba(0,0,0,.35);color:var(--white)}
.c1{left:52px}.c2{left:344px}.c3{left:636px}.c4{left:928px}
.r1{top:30px}.r2{top:176px}.r3{top:322px}.r4{top:467px}.r5{top:613px}.r6{top:759px}.r7{top:904px}.r8{top:1050px}
.a{position:absolute}
.h{left:24px;top:7px;font-weight:700;font-size:11px;color:var(--white);white-space:nowrap}
.hs{left:24px;top:21px;font-size:3px;color:var(--muted)}
.lead{font-size:7.5px;line-height:1.15;color:var(--white);font-weight:400}
.tx{font-size:3px;line-height:1.45;color:var(--body);text-align:justify}
.tx b,.sm b{color:var(--white)}
.sm{font-size:4px;line-height:1.3;color:var(--white);font-weight:600}
.blue{color:var(--sky)}
.caps{font-size:8.5px;line-height:1.05;text-transform:uppercase;color:var(--white);font-weight:300}
.caps b{font-weight:700}
.ft{position:absolute;left:24px;right:24px;bottom:3px;display:flex;justify-content:space-between;align-items:center;font-size:3px;color:var(--blue)}
.logo{display:flex;align-items:center;gap:2px;font-weight:700;font-size:4px;color:var(--white);letter-spacing:.2px}
.logo i{display:block;width:3px;height:3px;background:var(--blue)}
.ph{background:linear-gradient(135deg,#0a1a5a,#1e62ff 45%,#7b3cf0 75%,#0a0d28)}
.ph2{background:linear-gradient(140deg,#05222c,#0fa3b8 45%,#1a3f7a 80%,#08101e)}
.ph3{background:linear-gradient(130deg,#2a1650,#c0602a 40%,#3b5ab8 75%,#0c0f26)}
.dot{border-radius:50%}
.cols{display:grid;gap:10px}
ul.b{list-style:none}
ul.b li{font-size:3px;line-height:1.5;color:var(--body);padding-left:5px;position:relative}
ul.b li:before{content:"";position:absolute;left:0;top:1.3px;width:1.6px;height:1.6px;border-radius:50%;background:var(--white)}
ul.b li.s{padding-left:10px}
ul.b li.s:before{left:5px;border-radius:0;background:var(--sky)}
.num{display:flex;flex-direction:column;align-items:center;justify-content:center;border-radius:50%;background:var(--royal);color:#fff;font-weight:700}
.num small{font-size:2px;font-weight:400;color:#cfe0ff}
.yr{font-size:7px;font-weight:300}
.dash{border-top:.6px dashed #7d86a8}
.icon{width:9px;height:9px;border-radius:50%;background:var(--blue);display:flex;align-items:center;justify-content:center}
.icon:after{content:"";width:3px;height:3px;background:#fff;border-radius:1px}
</style>
</head>
<body>

<!-- Row 1 -->
<section class="slide c1 r1">
  <div class="a ph" style="inset:0" role="img" aria-label="Glowing blue circuit board with a processor chip"></div>
  <div class="a logo" style="left:24px;top:48px;font-size:17px;font-weight:600;gap:4px"><i style="width:6px;height:6px"></i>TALON</div>
  <div class="a" style="left:52px;top:66px;font-size:5px">Microsystems</div>
  <div class="a" style="left:24px;top:86px;font-weight:700;font-size:11px;line-height:1.2">Your presentation<br>title goes here</div>
  <div class="a" style="left:24px;top:114px;font-size:3.5px;font-weight:600">You could place a subtitle right here</div>
  <div class="a" style="left:24px;top:124px;font-size:7px;font-weight:600">Mark Talon</div>
  <div class="a" style="left:24px;top:134px;font-size:3.2px;font-weight:700;line-height:1.8">Founder &amp; CEO<br>Talon Microsystems</div>
</section>

<section class="slide c2 r1">
  <div class="a ph" style="inset:0" role="img" aria-label="Glowing blue circuit board with a processor chip"></div>
  <div class="a logo" style="left:24px;top:52px;font-size:15px;font-weight:600;gap:4px"><i style="width:6px;height:6px"></i>TALON</div>
  <div class="a" style="left:48px;top:68px;font-size:4.5px;color:var(--blue)">Microsystems</div>
  <div class="a" style="left:24px;top:86px;font-weight:700;font-size:11px;line-height:1.2">Your presentation<br>title goes here</div>
  <div class="a" style="left:24px;top:114px;font-size:3.5px;font-weight:600">You could place a subtitle right here</div>
  <div class="a" style="left:24px;top:124px;font-size:7px;font-weight:600">Mark Talon</div>
  <div class="a" style="left:24px;top:134px;font-size:3.2px;font-weight:700;line-height:1.8">Founder &amp; CEO<br>Talon Microsystems</div>
</section>

<section class="slide c3 r1">
  <div class="a h">Our Company Mision</div>
  <div class="a ph dot" style="left:52px;top:58px;width:40px;height:40px;border:1.5px solid #fff" role="img" aria-label="Portrait of the company founder"></div>
  <div class="a" style="left:36px;top:104px;width:72px;text-align:center;font-size:5px;line-height:1.25">Lorem Ipsum is simply dummy text of the printing industry.</div>
  <div class="a" style="left:62px;top:138px;font-size:2.5px;color:var(--muted)">Mark Talon</div>
  <div class="a" style="left:128px;top:58px;height:90px;border-left:.6px solid #3a4366"></div>
  <div class="a lead blue" style="left:140px;top:60px;width:190px;font-size:6px;color:var(--blue)">There are many variations<br>of passages of Lorem Ipsum available</div>
  <p class="a tx" style="left:140px;top:84px;width:150px">Lorem ipsum is simply dummy text of the printing and typesetting industry. It has been the standard sample text since the 1500s, when a printer scrambled a galley of type to make a specimen book. It survived five centuries and the leap into electronic typesetting, remaining essentially unchanged. It was popularised with sheets containing passages and later with desktop publishing software.</p>
  <div class="ft"><span class="logo"><i></i>TALON</span><span>Talon Microsystems Confidential</span><span>3</span></div>
</section>

<section class="slide c4 r1">
  <div class="a h">Header and Content Text 1 column</div>
  <div class="a hs">Lorem ipsum available, but the majority have suffered alteration.</div>
  <div class="a lead" style="left:24px;top:32px;font-size:6px">There are many variations<br>of passages of Lorem Ipsum available</div>
  <div class="a" style="left:24px;top:54px;width:316px">
    <p class="tx">Lorem ipsum dolor sit amet, consectetur adipiscing elit. Donec mauris lorem, vestibulum ac rutrum id, suscipit in dui. Donec vitae dapibus tellus. Vestibulum nunc sem, finibus quis elementum ac, varius ac tellus. Nam faucibus faucibus venenatis. Donec nec arcu velit. Fusce viverra, dui vitae euismod mollis, tortor magna egestas nunc, et suscipit nunc ex quis nunc. Pellentesque habitant morbi tristique senectus et netus.</p><br>
    <p class="tx">Nulla efficitur urna et massa dapibus maximus. Maecenas sit amet neque pretium, sagittis dui ut, consectetur purus. Phasellus auctor consectetur arcu a congue. Vestibulum congue sed orci efficitur finibus. Integer malesuada finibus ligula, aliquet lobortis nulla commodo vel.</p><br>
    <p class="tx">Nulla varius vehicula augue, id placerat nisi luctus a. Suspendisse magna tellus, imperdiet id turpis in, gravida fermentum sem. Integer commodo pharetra dui a congue. Vivamus in commodo dui. Nulla fringilla ex sapien, sit amet sed pretium ultricies. In hac habitasse platea dictumst. Donec lacinia efficitur dictum.</p>
  </div>
  <div class="ft"><span class="logo"><i></i>TALON</span><span>Talon Microsystems Confidential</span><span>4</span></div>
</section>

<!-- Row 2 -->
<section class="slide c1 r2">
  <div class="a h">Header and Content Text 2 column</div>
  <div class="a hs">Lorem ipsum available, but the majority have suffered alteration.</div>
  <div class="a lead" style="left:24px;top:32px;font-size:6px">There are many variations Lorem ipsum dolor sit amet, consectetur<br>adipiscing elit of passages of Lorem Ipsum available</div>
  <div class="a cols" style="left:24px;top:56px;width:316px;grid-template-columns:1fr 1fr">
    <p class="tx">Lorem ipsum is simply dummy text of the printing and typesetting industry. It has been the standard sample text since the 1500s, when a printer scrambled a galley of type to make a specimen book. It survived five centuries and the leap into electronic typesetting, remaining essentially unchanged. It was popularised with sheets of passages and later with desktop publishing software. It is a long established fact that a reader will be distracted by readable content when looking at a layout, so a sample keeps attention on the form.</p>
    <p class="tx">Many web sites are still in their infancy and various versions have evolved over the years. Contrary to popular belief, sample text is not simply random. It has roots in a piece of classical literature from 45 BC, making it over 2000 years old. A professor looked up one of the more obscure words, and going through the cites of the word in classical literature, discovered the source. The passage comes from sections of a treatise on the theory of ethics, very popular during the Renaissance.</p>
  </div>
  <div class="ft"><span class="logo"><i></i>TALON</span><span>Talon Microsystems Confidential</span><span>5</span></div>
</section>

<section class="slide c2 r2">
  <div class="a h">Three column text Slide</div>
  <div class="a cols" style="left:24px;top:28px;width:316px;grid-template-columns:1fr 1fr 1fr">
    <div><div class="sm">Lorem Ipsum is simply<br>dummy text</div><p class="tx" style="margin-top:4px">Lorem ipsum is simply dummy text of the printing and typesetting industry. It has been the standard sample text since the 1500s, when a printer scrambled a galley of type to make a specimen book. It survived five centuries and the leap into electronic typesetting, remaining essentially unchanged. It was popularised with sheets of passages and later with desktop publishing software.</p></div>
    <div><div class="sm">Lorem Ipsum is simply<br>dummy text</div><p class="tx" style="margin-top:4px">Lorem ipsum is simply dummy text of the printing and typesetting industry. It has been the standard sample text since the 1500s, when a printer scrambled a galley of type to make a specimen book. It survived five centuries and the leap into electronic typesetting, remaining essentially unchanged. It was popularised with sheets of passages and later with desktop publishing software.</p></div>
    <div><div class="sm">Lorem Ipsum is simply<br>dummy text</div><p class="tx" style="margin-top:4px">Lorem ipsum is simply dummy text of the printing and typesetting industry. It has been the standard sample text since the 1500s, when a printer scrambled a galley of type to make a specimen book. It survived five centuries and the leap into electronic typesetting, remaining essentially unchanged. It was popularised with sheets of passages and later with desktop publishing software.</p></div>
  </div>
  <div class="ft"><span class="logo"><i></i>TALON</span><span>Talon Microsystems Confidential</span><span>6</span></div>
</section>

<section class="slide c3 r2">
  <div class="a h">Overview 2 Column</div>
  <div class="a hs">Lorem ipsum, giving information on its origins, as well as a random text here</div>
  <div class="a lead" style="left:24px;top:30px;width:316px;font-size:6px">Lorem Ipsum is simply dummy text of the printing and typesetting industry. Lorem Ipsum has been the industry's standard dummy</div>
  <div class="a cols" style="left:24px;top:58px;width:316px;grid-template-columns:1fr 1fr;gap:16px">
    <div><div class="sm" style="font-size:3.6px">What is Lorem Ipsum?</div><p class="tx" style="margin-top:4px">Lorem ipsum is simply dummy text of the printing and typesetting industry. It has been the standard sample text since the 1500s, when a printer scrambled a galley of type to make a specimen book. It survived five centuries and the leap into electronic typesetting, remaining essentially unchanged with later desktop publishing software.</p></div>
    <div><div class="sm" style="font-size:3.6px">Why do we use it?</div><p class="tx" style="margin-top:4px">Lorem ipsum is simply dummy text of the printing and typesetting industry. It has been the standard sample text since the 1500s, when a printer scrambled a galley of type to make a specimen book. It survived five centuries and the leap into electronic typesetting, remaining essentially unchanged with later desktop publishing software.</p></div>
  </div>
  <div class="ft"><span class="logo"><i></i>TALON</span><span>Talon Microsystems Confidential</span><span>7</span></div>
</section>

<section class="slide c4 r2">
  <div class="a h">Header and Content Text 2 Bullet column</div>
  <div class="a hs">Lorem ipsum available, but the majority have suffered alteration.</div>
  <div class="a lead" style="left:24px;top:32px;font-size:6px">There are many variations Lorem ipsum dolor sit amet, consectetur<br>adipiscing elit of passages of Lorem Ipsum available</div>
  <div class="a cols" style="left:24px;top:56px;width:316px;grid-template-columns:1fr 1fr">
    <ul class="b"><li>Lorem ipsum dolor sit amet, consectetur adipiscing elit. Donec mauris lorem, vestibulum ac rutrum id, suscipit in dui.</li><li class="s">Vestibulum nunc sem, finibus quis elementum ac, varius ac tellus</li><li class="s">Nam faucibus faucibus venenatis. Donec nec arcu velit</li><li>Pellentesque habitant morbi tristique senectus et netus et malesuada fames ac turpis egestas.</li><li class="s">Tincidunt eleifend consequat</li><li class="s">Nulla efficitur urna et massa dapibus</li></ul>
    <ul class="b"><li>Lorem ipsum dolor sit amet, consectetur adipiscing elit. Donec mauris lorem, vestibulum ac rutrum id, suscipit in dui.</li><li class="s">Vestibulum nunc sem, finibus quis elementum ac, varius ac tellus</li><li class="s">Nam faucibus faucibus venenatis. Donec nec arcu velit</li><li>Pellentesque habitant morbi tristique senectus et netus et malesuada fames ac turpis egestas.</li><li class="s">Tincidunt eleifend consequat</li><li class="s">Nulla efficitur urna et massa dapibus</li></ul>
  </div>
  <div class="ft"><span class="logo"><i></i>TALON</span><span>Talon Microsystems Confidential</span><span>8</span></div>
</section>

<!-- Row 3 -->
<section class="slide c1 r3">
  <div class="a h">Header and Content Text 3 column</div>
  <div class="a hs">Lorem ipsum available, but the majority have suffered alteration.</div>
  <div class="a cols" style="left:24px;top:32px;width:316px;grid-template-columns:1fr 1fr 1fr">
    <p class="tx">Lorem ipsum is simply dummy text of the printing and typesetting industry. It has been the standard sample text since the 1500s, when a printer scrambled a galley of type to make a specimen book. It survived five centuries and the leap into electronic typesetting, remaining essentially unchanged. It was popularised with sheets of passages and later with desktop publishing software. It is a long established fact that a reader will be distracted by readable content of a page when looking at its layout, so sample text keeps attention on form.</p>
    <p class="tx">A more normal distribution of letters, as opposed to using plain repeated words, makes it look like readable English. Many publishing packages and web page editors now use sample text as their default model, and a search will uncover many sites still in their infancy. Various versions have evolved over the years, sometimes by accident, sometimes on purpose. Contrary to popular belief, it is not simply random text and has roots in classical literature from 45 BC.</p>
    <p class="tx">A professor looked up one of the more obscure words in a passage, and going through the cites of the word in classical literature, discovered the undoubtable source. It comes from sections of a treatise on the theory of ethics, very popular during the Renaissance. The standard chunk used since the 1500s is reproduced below for those interested, accompanied by English versions from a later translation.</p>
  </div>
  <div class="ft"><span class="logo"><i></i>TALON</span><span>Talon Microsystems Confidential</span><span>9</span></div>
</section>

<section class="slide c2 r3">
  <div class="a hs" style="top:10px">Lorem ipsum available, but the majority have suffered alteration.</div>
  <div class="a cols" style="left:24px;top:22px;width:316px;grid-template-columns:repeat(4,1fr);gap:8px">
    <p class="tx">Lorem ipsum is simply dummy text of the printing and typesetting industry. It has been the standard sample text since the 1500s, when a printer scrambled a galley of type to make a specimen book. It survived five centuries and the leap into electronic typesetting, remaining essentially unchanged. It was popularised with sheets of passages and later desktop publishing.</p>
    <p class="tx">The readable content of a page distracts a reader looking at its layout. A normal spread of letters makes it look readable. Many publishing packages and web page editors use sample text as their default model, and a search uncovers many sites still in their infancy, with versions evolving over years.</p>
    <p class="tx">A piece of classical Latin literature from 45 BC makes it over 2000 years old. A professor looked up one of the obscure words in a passage and, going through the cites in classical literature, discovered the source in a treatise on ethics popular during the Renaissance period.</p>
    <p class="tx">The standard chunk used since the 1500s is reproduced below for those interested. Sections from the treatise are also reproduced in their exact original form, accompanied by English versions from a later translation. Sample text is not simply random text and has a long history.</p>
  </div>
  <div class="ft"><span class="logo"><i></i>TALON</span><span>Talon Microsystems Confidential</span><span>10</span></div>
</section>

<section class="slide c3 r3">
  <div class="a h">Our Service</div>
  <div class="a hs">Lorem ipsum available, but the majority have suffered alteration.</div>
  <div class="a caps" style="left:0;right:0;top:44px;text-align:center;font-size:7px">We could help for select the <b>best</b><br><b>semiconductors</b> for your business</div>
  <p class="a tx" style="left:70px;top:74px;width:224px;text-align:center">Lorem ipsum simply random randomised words which look even slightly believable in some form, by injected humour or words which don't look even slightly believable in some form, by injected humour.</p>
  <div class="a" style="left:64px;top:128px;width:236px;height:3px;background:var(--royal)"></div>
  <div class="a num" style="left:56px;top:113px;width:32px;height:32px;font-size:7px;background:var(--blue)">2768<small>Product Portofolio</small></div>
  <div class="a num" style="left:118px;top:113px;width:32px;height:32px;font-size:7px;background:var(--blue)">657<small>Good Customer</small></div>
  <div class="a num" style="left:180px;top:113px;width:32px;height:32px;font-size:7px;background:var(--blue)">1768<small>Reliable Design</small></div>
  <div class="a num" style="left:242px;top:113px;width:32px;height:32px;font-size:7px;background:var(--blue)">987<small>Article &amp; Ads</small></div>
  <div class="ft"><span class="logo"><i></i>TALON</span><span>Talon Microsystems Confidential</span><span>14</span></div>
</section>

<section class="slide c4 r3">
  <div class="a caps" style="left:14px;top:22px;font-size:7px">We offer help<br>you to <b>select</b><br>the <b>best</b><br><b>semiconductors</b><br>for your<br>business</div>
  <p class="a tx" style="left:14px;top:78px;width:80px">Lorem ipsum is simply dummy text of the printing and typesetting industry. It has been the standard sample text since the 1500s, when a printer scrambled a galley of type to make a specimen book. It has survived not only five centuries.</p>
  <svg class="a" style="left:100px;top:0" width="264" height="200" viewBox="0 0 264 200" aria-hidden="true">
    <g stroke="#1f5bff" stroke-width="3" fill="none">
      <path d="M40 30 L90 30 L120 60 L170 60 L200 25"/>
      <path d="M50 90 L90 90 L120 60"/>
      <path d="M120 60 L140 85 L180 85 L200 85"/>
      <path d="M140 85 L140 150 L130 160"/>
      <path d="M200 25 L230 20"/>
    </g>
    <g fill="#1f5bff"><circle cx="40" cy="30" r="15"/><circle cx="200" cy="25" r="15"/><circle cx="50" cy="90" r="16"/><circle cx="140" cy="85" r="15"/><circle cx="200" cy="85" r="14"/><circle cx="130" cy="160" r="16"/></g>
    <g fill="none" stroke="#1f5bff" stroke-width="3"><circle cx="120" cy="60" r="6"/><circle cx="230" cy="20" r="4"/></g>
    <g fill="#fff" font-family="Montserrat, sans-serif" font-weight="700" font-size="9" text-anchor="middle"><text x="40" y="32">2768</text><text x="200" y="28">657</text><text x="50" y="92">1768</text><text x="140" y="88">987</text><text x="200" y="88">150</text><text x="130" y="163">10000</text></g>
  </svg>
  <div class="ft"><span class="logo"><i></i>TALON</span><span>Talon Microsystems Confidential</span><span>15</span></div>
</section>

<!-- Row 4: timelines -->
<section class="slide c1 r4">
  <div class="a h" style="top:14px;font-size:11.5px">Timeline</div>
  <div class="a num" style="left:14px;top:34px;width:20px;height:20px;font-size:4px;font-weight:400;background:var(--blue)">start</div>
  <div class="a sm" style="left:42px;top:36px;font-size:3px">Description</div>
  <p class="a tx" style="left:42px;top:42px;width:150px">Lorem ipsum dolor sit amet, consectetur adipiscing elit. Donec mauris lorem, vestibulum ac rutrum id, suscipit in dui. Donec vitae dapibus tellus, finibus quis elementum.</p>
  <div class="a dash" style="left:24px;right:20px;top:66px"></div>
  <div class="a cols" style="left:24px;top:76px;width:300px;grid-template-columns:repeat(3,1fr);gap:14px">
    <div><div class="yr">2017</div><div class="sm" style="font-size:2.6px;margin:5px 0 3px">Your first title goes here:</div><p class="tx">Lorem ipsum dolor sit amet, consectetur adipiscing elit. Donec mauris lorem, vestibulum ac rutrum id, suscipit in dui.</p></div>
    <div><div class="yr">2019</div><div class="sm" style="font-size:2.6px;margin:5px 0 3px">Your second title goes here:</div><p class="tx">Lorem ipsum dolor sit amet, consectetur adipiscing elit. Donec mauris lorem, vestibulum ac rutrum id, suscipit in dui.</p></div>
    <div><div class="yr">2021</div><div class="sm" style="font-size:2.6px;margin:5px 0 3px">Your third title goes here:</div><p class="tx">Lorem ipsum dolor sit amet, consectetur adipiscing elit. Donec mauris lorem, vestibulum ac rutrum id, suscipit in dui.</p></div>
  </div>
  <div class="ft"><span class="logo"><i></i>TALON</span><span>Talon Microsystems Confidential</span><span>11</span></div>
</section>

<section class="slide c2 r4">
  <div class="a h" style="top:14px;font-size:11.5px">Timeline</div>
  <div class="a sm" style="left:14px;top:36px;font-size:3px">Description</div>
  <p class="a tx" style="left:14px;top:42px;width:150px">Lorem ipsum dolor sit amet, consectetur adipiscing elit. Donec mauris lorem, vestibulum ac rutrum id, suscipit in dui. Donec vitae dapibus tellus.</p>
  <div class="a sm" style="left:186px;top:36px;font-size:3px">Description</div>
  <p class="a tx" style="left:186px;top:42px;width:150px">Lorem ipsum dolor sit amet, consectetur adipiscing elit. Donec mauris lorem, vestibulum ac rutrum id, suscipit in dui. Donec vitae dapibus tellus.</p>
  <div class="a dash" style="left:14px;right:14px;top:62px"></div>
  <div class="a cols" style="left:14px;top:76px;width:326px;grid-template-columns:repeat(4,1fr);gap:12px">
    <div><div class="yr">2022</div><div class="sm" style="font-size:2.6px;margin:5px 0 3px">Your first title goes here:</div><p class="tx">Lorem ipsum dolor sit amet, consectetur adipiscing elit. Donec mauris lorem, vestibulum ac rutrum id.</p></div>
    <div><div class="yr">2023</div><div class="sm" style="font-size:2.6px;margin:5px 0 3px">Your first title goes here:</div><p class="tx">Lorem ipsum dolor sit amet, consectetur adipiscing elit. Donec mauris lorem, vestibulum ac rutrum id.</p></div>
    <div><div class="yr">2024</div><div class="sm" style="font-size:2.6px;margin:5px 0 3px">Your first title goes here:</div><p class="tx">Lorem ipsum dolor sit amet, consectetur adipiscing elit. Donec mauris lorem, vestibulum ac rutrum id.</p></div>
    <div><div class="yr">2025</div><div class="sm" style="font-size:2.6px;margin:5px 0 3px">Your first title goes here:</div><p class="tx">Lorem ipsum dolor sit amet, consectetur adipiscing elit. Donec mauris lorem, vestibulum ac rutrum id.</p></div>
  </div>
  <div class="ft"><span class="logo"><i></i>TALON</span><span>Talon Microsystems Confidential</span><span>12</span></div>
</section>

<section class="slide c3 r4">
  <div class="a h" style="top:14px;font-size:11.5px">Timeline</div>
  <div class="a sm" style="left:24px;top:36px;font-size:3px">Description</div>
  <p class="a tx" style="left:24px;top:42px;width:260px">Lorem ipsum dolor sit amet, consectetur adipiscing elit. Donec mauris lorem, vestibulum ac rutrum id, suscipit in dui. Donec vitae dapibus tellus. Vestibulum nunc sem, finibus quis elementum ac, varius ac tellus.</p>
  <div class="a num" style="left:328px;top:34px;width:20px;height:20px;font-size:4px;font-weight:400;background:var(--blue)">End</div>
  <div class="a dash" style="left:24px;right:20px;top:66px"></div>
  <div class="a cols" style="left:24px;top:76px;width:260px;grid-template-columns:repeat(3,1fr);gap:14px">
    <div><div class="yr">2026</div><div class="sm" style="font-size:2.6px;margin:5px 0 3px">Your first title goes here:</div><p class="tx">Lorem ipsum dolor sit amet, consectetur adipiscing elit. Donec mauris lorem, vestibulum ac rutrum id, suscipit in dui.</p></div>
    <div><div class="yr">2027</div><div class="sm" style="font-size:2.6px;margin:5px 0 3px">Your first title goes here:</div><p class="tx">Lorem ipsum dolor sit amet, consectetur adipiscing elit. Donec mauris lorem, vestibulum ac rutrum id, suscipit in dui.</p></div>
    <div><div class="yr">2028</div><div class="sm" style="font-size:2.6px;margin:5px 0 3px">Your first title goes here:</div><p class="tx">Lorem ipsum dolor sit amet, consectetur adipiscing elit. Donec mauris lorem, vestibulum ac rutrum id, suscipit in dui.</p></div>
  </div>
  <div class="ft"><span class="logo"><i></i>TALON</span><span>Talon Microsystems Confidential</span><span>13</span></div>
</section>

<section class="slide c4 r4">
  <div class="a ph3" style="left:0;top:0;width:364px;height:120px" role="img" aria-label="Close-up of a processor chip on a circuit board"></div>
  <div class="a sm" style="left:24px;top:132px;font-size:4.5px">Lorem ipsum caption placeholder</div>
  <p class="a tx" style="left:24px;top:142px;width:150px">Lorem ipsum random randomised words which don't look even slightly believable in some form, by injected humour, or words which don't look even slightly believable.</p>
  <div class="a caps" style="left:194px;top:134px;font-size:5.5px">We could help for select<br>the best semiconductors<br>for your business</div>
  <div class="ft"><span class="logo"><i></i>TALON</span><span>Talon Microsystems Confidential</span><span>16</span></div>
</section>

<!-- Row 5 -->
<section class="slide c1 r5">
  <div class="a h" style="left:26px;top:10px;font-size:7px">About Us</div>
  <div class="a" style="left:26px;top:30px;font-size:9.5px">Our Products</div>
  <div class="a sm" style="left:26px;top:44px;font-size:4.5px;font-weight:400">Lorem Ipsum is simply dummy text</div>
  <p class="a tx" style="left:26px;top:54px;width:130px">Lorem ipsum is simply dummy text of the printing and typesetting industry. It has been the industry's standard dummy text ever since the 1500s, survived not only five centuries, but also the leap into electronic typesetting, remaining essentially unchanged. It was popularised in the 1960s with the release of sheets.</p>
  <div class="a cols" style="left:26px;top:96px;width:120px;grid-template-columns:1fr 1fr;gap:4px">
    <ul class="b"><li>Ipsum dummy text</li><li>Ipsum dummy text</li><li>Ipsum dummy text</li><li>Ipsum dummy text</li></ul>
    <ul class="b"><li>Ipsum dummy text</li><li>Ipsum dummy text</li><li>Ipsum dummy text</li><li>Ipsum dummy text</li></ul>
  </div>
  <div class="a" style="left:186px;top:30px;width:150px;height:140px;display:grid;grid-template-columns:repeat(3,1fr);gap:2px" role="img" aria-label="Grid of nine processor chip photos">
    <div class="ph"></div><div class="ph3"></div><div class="ph"></div><div class="ph2"></div><div class="ph3"></div><div class="ph"></div><div class="ph"></div><div class="ph2"></div><div class="ph3"></div>
  </div>
  <div class="ft"><span class="logo"><i></i>TALON</span><span>Talon Microsystems Confidential</span><span>17</span></div>
</section>

<section class="slide c2 r5">
  <div class="a h">What We Do ?</div>
  <p class="a tx" style="left:24px;top:24px;width:316px">Lorem ipsum available, but the majority have suffered alteration. Lorem ipsum dolor sit amet, consectetur adipiscing elit. Donec mauris lorem, vestibulum ac rutrum id, suscipit in dui. Donec vitae dapibus tellus. Vestibulum nunc sem, finibus quis elementum ac, varius ac tellus. Nam faucibus faucibus venenatis. Donec nec arcu velit. Fusce viverra, dui vitae euismod mollis, tortor magna egestas nunc, et suscipit nunc ex quis nunc. Pellentesque habitant morbi tristique senectus.</p>
  <div class="a cols" style="left:24px;top:50px;width:316px;grid-template-columns:repeat(4,1fr);gap:8px">
    <div><div class="ph" style="height:78px" role="img" aria-label="Glowing chip on circuit board"></div><p class="tx" style="margin-top:4px;text-align:center">This standard defines an onerous contract in which the unavoidable costs of meeting</p></div>
    <div><div class="ph3" style="height:78px" role="img" aria-label="Chip with warm light"></div><p class="tx" style="margin-top:4px;text-align:center">This standard defines an onerous contract in which the unavoidable costs of meeting</p></div>
    <div><div class="ph" style="height:78px" role="img" aria-label="Processor on blue board"></div><p class="tx" style="margin-top:4px;text-align:center">This standard defines an onerous contract in which the unavoidable costs of meeting</p></div>
    <div><div class="ph2" style="height:78px" role="img" aria-label="Teal lit circuit board"></div><p class="tx" style="margin-top:4px;text-align:center">This standard defines an onerous contract in which the unavoidable costs of meeting</p></div>
  </div>
  <div class="ft"><span class="logo"><i></i>TALON</span><span>Talon Microsystems Confidential</span><span>18</span></div>
</section>

<section class="slide c3 r5">
  <div class="a h">What We Do ?</div>
  <p class="a tx" style="left:24px;top:24px;width:316px">Lorem ipsum available, but the majority have suffered alteration. Lorem ipsum dolor sit amet, consectetur adipiscing elit. Donec mauris lorem, vestibulum ac rutrum id, suscipit in dui. Donec vitae dapibus tellus. Vestibulum nunc sem, finibus quis elementum ac, varius ac tellus. Nam faucibus faucibus venenatis. Donec nec arcu velit. Fusce viverra, dui vitae euismod mollis.</p>
  <div class="a cols" style="left:24px;top:46px;width:316px;grid-template-columns:repeat(3,1fr);gap:10px">
    <div><div class="ph" style="height:76px" role="img" aria-label="Processor on blue board"></div><p class="tx" style="margin-top:4px">Lorem ipsum dolor sit amet, consectetur adipiscing elit. Donec mauris lorem, vestibulum ac rutrum id, suscipit in dui. Donec vitae dapibus tellus.</p></div>
    <div><div class="ph2" style="height:76px" role="img" aria-label="Teal lit circuit board"></div><p class="tx" style="margin-top:4px">Lorem ipsum dolor sit amet, consectetur adipiscing elit. Donec mauris lorem, vestibulum ac rutrum id, suscipit in dui. Donec vitae dapibus tellus.</p></div>
    <div><div class="ph3" style="height:76px" role="img" aria-label="Chip with warm light"></div><p class="tx" style="margin-top:4px">Lorem ipsum dolor sit amet, consectetur adipiscing elit. Donec mauris lorem, vestibulum ac rutrum id, suscipit in dui. Donec vitae dapibus tellus.</p></div>
  </div>
  <div class="ft"><span class="logo"><i></i>TALON</span><span>Talon Microsystems Confidential</span><span>19</span></div>
</section>

<section class="slide c4 r5">
  <div class="a h">Image with 2 Column Text</div>
  <div class="a hs">Lorem ipsum available, but the majority have suffered alteration.</div>
  <div class="a ph3" style="left:0;top:30px;width:84px;height:150px" role="img" aria-label="Processor chip close-up"></div>
  <div class="a" style="left:92px;top:30px;width:118px">
    <div class="sm" style="font-size:5px">Best Presentation</div>
    <div style="font-size:5px;line-height:1.1">Layout with Two<br>Columns</div>
    <div style="font-size:4px;color:var(--body);margin:4px 0 3px">Image and Description</div>
    <p class="tx">Lorem ipsum is simply dummy text of the printing and typesetting industry. It has been the industry's standard dummy text ever since the 1500s, when an unknown printer took a galley of type and scrambled it to make a type specimen book. It has survived not only five centuries, but also the leap into electronic typesetting, remaining essentially unchanged. It was popularised in the 1960s with the release of sheets containing passages.</p>
  </div>
  <p class="a tx" style="left:224px;top:30px;width:116px">Contrary to popular belief, Lorem Ipsum is not simply random text. It has roots in a piece of classical Latin literature from 45 BC, making it over 2000 years old. A professor at a college looked up one of the more obscure Latin words from a passage, and going through the cites of the word in classical literature, discovered the undoubtable source. It comes from sections of a treatise on the theory of ethics, very popular during the Renaissance. The first line of the passage comes from a line in that section.</p>
  <div class="ft"><span class="logo"><i></i>TALON</span><span>Talon Microsystems Confidential</span><span>20</span></div>
</section>

<!-- Row 6 -->
<section class="slide c1 r6">
  <div class="a ph dot" style="left:38px;top:30px;width:80px;height:80px;border:2px solid #fff" role="img" aria-label="Portrait of a smiling engineer holding a circuit board"></div>
  <div class="a" style="left:140px;top:54px;font-size:9px;font-weight:700">“</div>
  <div class="a sm" style="left:146px;top:62px;width:170px;font-size:5.5px;line-height:1.25">Talon has a very talented team, who love coming to work and immersing themselves in all things”.</div>
  <div class="a" style="left:220px;top:112px;font-size:4px;text-align:center;line-height:1.2">Owen Ridley<br><span style="font-size:2.8px">FOUNDER &amp; CEO<br>Ridley Electric, Co</span></div>
  <div class="ft"><span class="logo"><i></i>TALON</span><span>Talon Microsystems Confidential</span><span>21</span></div>
</section>

<section class="slide c2 r6">
  <div class="a h">What We Do ?</div>
  <div class="a hs">Lorem ipsum available, but the majority have suffered alteration.</div>
  <div class="a ph2" style="left:24px;top:40px;width:140px;height:116px" role="img" aria-label="Teal lit circuit board with chips"></div>
  <div class="a" style="left:174px;top:40px;width:160px;font-size:7px;line-height:1.15;font-weight:300">We have a great client<br>who love to treat us as<br>their partner.”</div>
  <p class="a tx" style="left:174px;top:78px;width:146px">Lorem ipsum random randomised words which don't look even slightly believable in some form, by injected humour, or words which don't look even slightly or randomised words which don't look even slightly believable in some form, or words which don't look even slightly. Words which don't look even slightly or randomised.</p>
  <div class="ft"><span class="logo"><i></i>TALON</span><span>Talon Microsystems Confidential</span><span>22</span></div>
</section>

<section class="slide c3 r6">
  <div class="a h">Our Portofolio</div>
  <div class="a hs">Lorem ipsum available, but the majority have suffered alteration.</div>
  <div class="a caps" style="left:24px;top:34px;font-size:6px">We offer help<br>you to <b>select</b><br>the <b>best</b><br><b>semiconductors</b><br>for your<br>business</div>
  <p class="a tx" style="left:24px;top:80px;width:78px">Lorem ipsum is simply dummy text of the printing and typesetting industry. It has been the industry's standard dummy text ever since the 1500s, when an unknown printer took a galley of type and scrambled it to make a type specimen book, and survived five centuries.</p>
  <div class="a ph2" style="left:126px;top:34px;width:64px;height:112px" role="img" aria-label="Teal circuit board"></div>
  <div class="a ph3" style="left:192px;top:34px;width:64px;height:112px" role="img" aria-label="Chip with orange light"></div>
  <div class="a ph" style="left:258px;top:34px;width:64px;height:112px" role="img" aria-label="Blue processor chip"></div>
  <div class="ft"><span class="logo"><i></i>TALON</span><span>Talon Microsystems Confidential</span><span>23</span></div>
</section>

<section class="slide c4 r6">
  <div class="a h">Our Portofolio</div>
  <div class="a hs">Lorem ipsum available, but the majority have suffered alteration.</div>
  <div class="a cols" style="left:24px;top:32px;width:316px;grid-template-columns:1fr 1fr;row-gap:12px">
    <div style="display:flex;gap:5px"><div class="ph" style="width:52px;height:52px;flex:none" role="img" aria-label="Blue chip"></div><div><div class="sm" style="font-size:3px;color:var(--sky)">Semiconductor #12345-6789</div><p class="tx" style="margin-top:3px">Lorem ipsum dolor sit amet, consectetur adipiscing elit. Donec mauris lorem, vestibulum ac rutrum id, suscipit in dui.</p></div></div>
    <div style="display:flex;gap:5px"><div class="ph2" style="width:52px;height:52px;flex:none" role="img" aria-label="Teal board"></div><div><div class="sm" style="font-size:3px;color:var(--sky)">Semiconductor #12345-6789</div><p class="tx" style="margin-top:3px">Lorem ipsum dolor sit amet, consectetur adipiscing elit. Donec mauris lorem, vestibulum ac rutrum id, suscipit in dui.</p></div></div>
    <div style="display:flex;gap:5px"><div class="ph3" style="width:52px;height:52px;flex:none" role="img" aria-label="Warm lit chip"></div><div><div class="sm" style="font-size:3px;color:var(--sky)">Semiconductor #12345-6789</div><p class="tx" style="margin-top:3px">Lorem ipsum dolor sit amet, consectetur adipiscing elit. Donec mauris lorem, vestibulum ac rutrum id, suscipit in dui.</p></div></div>
    <div style="display:flex;gap:5px"><div class="ph" style="width:52px;height:52px;flex:none" role="img" aria-label="Purple lit chip"></div><div><div class="sm" style="font-size:3px;color:var(--sky)">Semiconductor #12345-6789</div><p class="tx" style="margin-top:3px">Lorem ipsum dolor sit amet, consectetur adipiscing elit. Donec mauris lorem, vestibulum ac rutrum id, suscipit in dui.</p></div></div>
  </div>
  <div class="ft"><span class="logo"><i></i>TALON</span><span>Talon Microsystems Confidential</span><span>24</span></div>
</section>

<!-- Row 7 -->
<section class="slide c1 r7">
  <div class="a h">Our Service</div>
  <div class="a hs">Lorem ipsum available, but the majority have suffered alteration.</div>
  <div class="a cols" style="left:20px;top:30px;width:320px;grid-template-columns:1fr 1fr;row-gap:8px">
    <div style="display:flex;gap:6px"><span class="icon" style="flex:none"></span><div><div class="sm" style="font-size:3px">Semiconductor</div><p class="tx">Lorem ipsum randomised words which don't look even slightly believable in some form, by injected humour.</p></div></div>
    <div style="display:flex;gap:6px"><span class="icon" style="flex:none"></span><div><div class="sm" style="font-size:3px">Semiconductor</div><p class="tx">Lorem ipsum randomised words which don't look even slightly believable in some form, by injected humour.</p></div></div>
    <div style="display:flex;gap:6px"><span class="icon" style="flex:none"></span><div><div class="sm" style="font-size:3px">Semiconductor</div><p class="tx">Lorem ipsum randomised words which don't look even slightly believable in some form, by injected humour.</p></div></div>
    <div style="display:flex;gap:6px"><span class="icon" style="flex:none"></span><div><div class="sm" style="font-size:3px">Semiconductor</div><p class="tx">Lorem ipsum randomised words which don't look even slightly believable in some form, by injected humour.</p></div></div>
    <div style="display:flex;gap:6px"><span class="icon" style="flex:none"></span><div><div class="sm" style="font-size:3px">Semiconductor</div><p class="tx">Lorem ipsum randomised words which don't look even slightly believable in some form, by injected humour.</p></div></div>
    <div style="display:flex;gap:6px"><span class="icon" style="flex:none"></span><div><div class="sm" style="font-size:3px">Semiconductor</div><p class="tx">Lorem ipsum randomised words which don't look even slightly believable in some form, by injected humour.</p></div></div>
    <div style="display:flex;gap:6px"><span class="icon" style="flex:none"></span><div><div class="sm" style="font-size:3px">Semiconductor</div><p class="tx">Lorem ipsum randomised words which don't look even slightly believable in some form, by injected humour.</p></div></div>
    <div style="display:flex;gap:6px"><span class="icon" style="flex:none"></span><div><div class="sm" style="font-size:3px">Semiconductor</div><p class="tx">Lorem ipsum randomised words which don't look even slightly believable in some form, by injected humour.</p></div></div>
  </div>
  <div class="ft"><span class="logo"><i></i>TALON</span><span>Talon Microsystems Confidential</span><span>25</span></div>
</section>

<section class="slide c2 r7">
  <div class="a h">Our Service</div>
  <div class="a hs">Lorem ipsum available, but the majority have suffered alteration.</div>
  <div class="a cols" style="left:24px;top:34px;width:316px;grid-template-columns:repeat(3,1fr);row-gap:10px;text-align:center">
    <div><span class="icon" style="margin:0 auto"></span><div class="sm" style="font-size:3px;margin:3px 0 2px">Consultacy</div><p class="tx" style="text-align:center">Lorem ipsum randomised words which don't look even slightly believable in some form.</p></div>
    <div><span class="icon" style="margin:0 auto"></span><div class="sm" style="font-size:3px;margin:3px 0 2px">Graphic Design</div><p class="tx" style="text-align:center">Lorem ipsum randomised words which don't look even slightly believable in some form.</p></div>
    <div><span class="icon" style="margin:0 auto"></span><div class="sm" style="font-size:3px;margin:3px 0 2px">Marketing</div><p class="tx" style="text-align:center">Lorem ipsum randomised words which don't look even slightly believable in some form.</p></div>
    <div><span class="icon" style="margin:0 auto"></span><div class="sm" style="font-size:3px;margin:3px 0 2px">Event Management</div><p class="tx" style="text-align:center">Lorem ipsum randomised words which don't look even slightly believable in some form.</p></div>
    <div><span class="icon" style="margin:0 auto"></span><div class="sm" style="font-size:3px;margin:3px 0 2px">Management</div><p class="tx" style="text-align:center">Lorem ipsum randomised words which don't look even slightly believable in some form.</p></div>
    <div><span class="icon" style="margin:0 auto"></span><div class="sm" style="font-size:3px;margin:3px 0 2px">Computerizing</div><p class="tx" style="text-align:center">Lorem ipsum randomised words which don't look even slightly believable in some form.</p></div>
  </div>
  <div class="ft"><span class="logo"><i></i>TALON</span><span>Talon Microsystems Confidential</span><span>26</span></div>
</section>

<section class="slide c3 r7">
  <div class="a h">Pie Chart</div>
  <div class="a hs">Lorem ipsum available, but the majority have suffered alteration</div>
  <div class="a cols" style="left:24px;top:34px;width:316px;grid-template-columns:repeat(3,1fr);gap:12px;text-align:center">
    <div><div class="dot" style="width:46px;height:46px;margin:0 auto;background:conic-gradient(var(--cyan) 0 62%,var(--royal) 62% 88%,var(--sky) 88%);display:flex;align-items:center;justify-content:center"><div class="dot" style="width:28px;height:28px;background:var(--ink-2);font-size:3.8px;font-weight:700;display:flex;align-items:center;justify-content:center;line-height:1.1">Sales<br>Chart 01</div></div><div class="sm" style="font-size:3px;margin:6px 0 2px">Lorem ipsum is not simply</div><p class="tx" style="text-align:center">Contrary to popular belief, sample text is not simply random text with roots in classics.</p></div>
    <div><div class="dot" style="width:46px;height:46px;margin:0 auto;background:conic-gradient(var(--cyan) 0 62%,var(--royal) 62% 88%,var(--sky) 88%);display:flex;align-items:center;justify-content:center"><div class="dot" style="width:28px;height:28px;background:var(--ink-2);font-size:3.8px;font-weight:700;display:flex;align-items:center;justify-content:center;line-height:1.1">Sales<br>Chart 02</div></div><div class="sm" style="font-size:3px;margin:6px 0 2px">Lorem ipsum is not simply</div><p class="tx" style="text-align:center">Contrary to popular belief, sample text is not simply random text with roots in classics.</p></div>
    <div><div class="dot" style="width:46px;height:46px;margin:0 auto;background:conic-gradient(var(--cyan) 0 62%,var(--royal) 62% 88%,var(--sky) 88%);display:flex;align-items:center;justify-content:center"><div class="dot" style="width:28px;height:28px;background:var(--ink-2);font-size:3.8px;font-weight:700;display:flex;align-items:center;justify-content:center;line-height:1.1">Sales<br>Chart 03</div></div><div class="sm" style="font-size:3px;margin:6px 0 2px">Lorem ipsum is not simply</div><p class="tx" style="text-align:center">Contrary to popular belief, sample text is not simply random text with roots in classics.</p></div>
  </div>
  <div class="ft"><span class="logo"><i></i>TALON</span><span>Talon Microsystems Confidential</span><span>27</span></div>
</section>

<section class="slide c4 r7">
  <div class="a h">3D Data Chart</div>
  <div class="a hs">Lorem ipsum available, but the majority have suffered alteration.</div>
  <svg class="a" style="left:18px;top:30px" width="170" height="140" viewBox="0 0 170 140" aria-label="Bar chart for April, May and June" role="img">
    <g font-family="Montserrat, sans-serif" font-size="4" fill="#aab2c8">
      <text x="0" y="20">70</text><text x="0" y="42">56</text><text x="0" y="64">42</text><text x="0" y="86">28</text><text x="0" y="108">14</text><text x="2" y="128">0</text>
      <text x="30" y="136">April</text><text x="78" y="124">May</text><text x="124" y="118">June</text>
    </g>
    <g>
      <rect x="18" y="106" width="18" height="20" fill="#1433e0"/><rect x="38" y="70" width="14" height="56" fill="#1fc0ff"/>
      <rect x="62" y="96" width="18" height="20" fill="#1433e0"/><rect x="82" y="52" width="14" height="64" fill="#1fc0ff"/>
      <rect x="106" y="88" width="18" height="22" fill="#1433e0"/><rect x="126" y="30" width="14" height="80" fill="#1fc0ff"/>
      <rect x="146" y="20" width="10" height="90" fill="#1f5bff"/>
    </g>
  </svg>
  <div class="a caps" style="left:220px;top:40px;font-size:6.5px">We offer help<br>you to select the<br><b>best</b><br><b>semiconductors</b><br>for your business</div>
  <p class="a tx" style="left:220px;top:90px;width:120px">Lorem ipsum is simply dummy text of the printing and typesetting industry. It has been the industry's standard dummy text ever since the 1500s, when an unknown printer took a galley of type and scrambled it to make a type specimen book.</p>
  <div class="ft"><span class="logo"><i></i>TALON</span><span>Talon Microsystems Confidential</span><span>28</span></div>
</section>

<!-- Row 8 -->
<section class="slide c1 r8">
  <div class="a h">3D Data Chart</div>
  <div class="a hs">Lorem ipsum available, but the majority have suffered alteration.</div>
  <div class="a caps" style="left:24px;top:44px;font-size:6.5px">We offer help<br>you to <b>select</b> the<br><b>best</b><br><b>semiconductors</b><br>for your business</div>
  <p class="a tx" style="left:24px;top:96px;width:110px">Lorem ipsum is simply dummy text of the printing and typesetting industry. It has been the industry's standard dummy text ever since the 1500s, when an unknown printer took a galley of type and scrambled it to make a type specimen book.</p>
  <svg class="a" style="left:170px;top:40px" width="180" height="100" viewBox="0 0 180 100" role="img" aria-label="Pie chart with shares 53, 26 and 17">
    <ellipse cx="90" cy="56" rx="80" ry="36" fill="#0d2aa8"/>
    <ellipse cx="90" cy="48" rx="80" ry="36" fill="#1fc0ff"/>
    <path d="M90 48 L150 24 A80 36 0 0 1 120 82 Z" fill="#1433e0"/>
    <path d="M90 48 L90 12 A80 36 0 0 1 150 24 Z" fill="#1f5bff"/>
    <g font-family="Montserrat, sans-serif" font-size="9" fill="#fff"><text x="30" y="56">53</text><text x="132" y="60">26</text><text x="106" y="28">17</text></g>
  </svg>
  <div class="ft"><span class="logo"><i></i>TALON</span><span>Talon Microsystems Confidential</span><span>29</span></div>
</section>

<section class="slide c2 r8">
  <div class="a h">3D Area Data Chart</div>
  <div class="a hs">Lorem ipsum available, but the majority have suffered alteration.</div>
  <svg class="a" style="left:24px;top:34px" width="170" height="140" viewBox="0 0 170 140" role="img" aria-label="Area chart for region 1 and region 2">
    <g font-family="Montserrat, sans-serif" font-size="4.5" fill="#fff">
      <text x="0" y="52">100</text><text x="2" y="64">75</text><text x="2" y="76">50</text><text x="2" y="88">25</text><text x="6" y="100">0</text>
      <text x="60" y="10">Text here</text><text x="102" y="28">Text here</text>
      <text x="32" y="138">Region 1</text><text x="72" y="138">Region 2</text>
    </g>
    <circle cx="28" cy="136.5" r="1.4" fill="#1f5bff"/><circle cx="68" cy="136.5" r="1.4" fill="#1fc0ff"/>
    <path d="M18 98 L40 80 L70 66 L90 82 L110 58 L140 78 L140 98 Z" fill="#1433e0"/>
    <path d="M18 98 L40 88 L70 74 L90 86 L110 70 L140 84 L140 98 Z" fill="#1fc0ff"/>
    <path d="M80 14 L86 20 L92 14 Z" fill="#1f5bff"/><path d="M112 32 L118 38 L124 32 Z" fill="#1f5bff"/>
  </svg>
  <div class="a" style="left:206px;top:34px;width:140px;font-size:7px;line-height:1.15;font-weight:300"><b style="font-weight:700">The Best</b> Presentation Layout with <b style="font-weight:700">Area Chart</b> and Description.</div>
  <div class="a sm" style="left:206px;top:68px;font-size:3.6px">This is Layout with Two Columns<br>and Content Title</div>
  <p class="a tx" style="left:206px;top:82px;width:126px">Lorem ipsum is simply dummy text of the printing and typesetting industry. It has been the industry's standard dummy text ever since the 1500s, when an unknown printer took a galley of type and scrambled it to make a type specimen book. It has survived not only five centuries.</p>
  <div class="ft"><span class="logo"><i></i>TALON</span><span>Talon Microsystems Confidential</span><span>30</span></div>
</section>

<section class="slide c3 r8">
  <div class="a h">3D Data Chart</div>
  <div class="a hs">Lorem ipsum available, but the majority have suffered alteration.</div>
  <div class="a caps" style="left:24px;top:44px;font-size:6.5px">We offer help<br>you to <b>select</b> the<br><b>best</b><br><b>semiconductors</b><br>for your business</div>
  <p class="a tx" style="left:24px;top:96px;width:110px">Lorem ipsum is simply dummy text of the printing and typesetting industry. It has been the industry's standard dummy text ever since the 1500s, when an unknown printer took a galley of type and scrambled it to make a type specimen book.</p>
  <svg class="a" style="left:160px;top:28px" width="190" height="150" viewBox="0 0 190 150" role="img" aria-label="Horizontal bar chart">
    <g stroke="#2a3152" stroke-width=".4"><line x1="20" y1="4" x2="20" y2="140"/><line x1="50" y1="4" x2="50" y2="140"/><line x1="80" y1="4" x2="80" y2="140"/><line x1="110" y1="4" x2="110" y2="140"/><line x1="140" y1="4" x2="140" y2="140"/><line x1="170" y1="4" x2="170" y2="140"/></g>
    <rect x="20" y="6" width="140" height="8" fill="#1fc0ff"/><rect x="20" y="16" width="106" height="8" fill="#1433e0"/>
    <rect x="20" y="50" width="86" height="8" fill="#1fc0ff"/><rect x="20" y="60" width="52" height="8" fill="#1433e0"/>
    <rect x="20" y="100" width="118" height="8" fill="#1fc0ff"/><rect x="20" y="110" width="34" height="8" fill="#1433e0"/>
    <g font-family="Montserrat, sans-serif" font-size="5" fill="#fff"><text x="164" y="13">70</text><text x="130" y="23">53</text><text x="110" y="57">43</text><text x="76" y="67">26</text><text x="142" y="107">59</text><text x="56" y="117">17</text></g>
    <g font-family="Montserrat, sans-serif" font-size="3" fill="#aab2c8"><text x="6" y="16">June</text><text x="6" y="60">May</text><text x="6" y="110">April</text></g>
  </svg>
  <div class="ft"><span class="logo"><i></i>TALON</span><span>Talon Microsystems Confidential</span><span>31</span></div>
</section>

<section class="slide c4 r8">
  <div class="a ph" style="left:0;top:0;width:364px;height:150px" role="img" aria-label="Glowing violet circuit board with processor chip"></div>
  <div class="a" style="left:0;right:0;top:126px;text-align:center;font-size:10px;letter-spacing:.3px"><b>KEEP IN TOUCH</b> WITH US</div>
  <div class="a" style="left:0;right:0;top:150px;bottom:0;background:linear-gradient(90deg,var(--royal),var(--blue) 60%,var(--cyan))"></div>
  <div class="a" style="left:72px;top:156px;font-size:3px;line-height:1.5"><b>ADDRESS</b><br>18 Harbor Lane, Oakmont,<br>California, CA 94010</div>
  <div class="a" style="left:158px;top:156px;font-size:3px;line-height:1.5"><b>PHONE &amp; EMAIL</b><br>hello@talonmicro.example<br>+1 555-014-2290</div>
  <div class="a" style="left:240px;top:156px;font-size:3px;line-height:1.5"><b>FOLLOW US</b></div>
  <div class="a" style="left:240px;top:164px;display:flex;gap:4px"><span class="dot" style="width:4px;height:4px;background:#fff"></span><span class="dot" style="width:4px;height:4px;background:#fff"></span><span class="dot" style="width:4px;height:4px;background:#fff"></span></div>
  <div class="a" style="left:0;right:0;bottom:4px;text-align:center;font-size:3px;color:#dfe8ff">Talon Microsystems Confidential</div>
  <div class="a" style="right:24px;bottom:4px;font-size:3px">32</div>
</section>

</body>
</html>
```